Business Card Design Project

Looking to update our business cards. We have a logo with our slogan. We are an IT firm so we wouldlike a modern look.

Industry/Entity Type

Business

```html
<!DOCTYPE html>
<html lang="en">
<head>
<meta charset="utf-8">
<title>Nexbyte Inc — Business Card Concepts</title>
<link href="https://fonts.googleapis.com/css2?family=Josefin+Sans:wght@400;600&display=swap" rel="stylesheet">
<style>
  :root {
    --backdrop: #4a2c1e;
    --green-light: #9dbb42;
    --green-mid: #7a963c;
    --green-dark: #6a8536;
    --band-green: #222b14;
    --band-grey: #222222;
    --grey-light: #d3d3d5;
    --grey-mid: #a4a4a6;
    --logo-green: #5c7a2e;
    --logo-accent: #9dc23a;
    --slogan: #f2f2f0;
  }
  * { margin: 0; padding: 0; box-sizing: border-box; }
  html, body {
    width: 1200px;
    height: 1181px;
    overflow: hidden;
  }
  body {
    background: var(--backdrop);
    position: relative;
    font-family: "Josefin Sans", sans-serif;
  }
  .card {
    position: absolute;
    left: 182px;
    width: 836px;
    height: 481px;
    overflow: hidden;
  }
  .card--green {
    top: 74px;
    background: radial-gradient(ellipse 60% 65% at 50% 52%, var(--green-light) 0%, var(--green-mid) 65%, var(--green-dark) 100%);
  }
  .card--grey {
    top: 617px;
    background: radial-gradient(ellipse 60% 65% at 50% 52%, var(--grey-light) 0%, #bdbdbf 55%, var(--grey-mid) 100%);
  }
  .card__band {
    position: absolute;
    left: 0;
    top: 181px;
    width: 100%;
    height: 119px;
    box-shadow: 0 3px 6px rgba(0,0,0,0.25);
  }
  .card--green .card__band { background: var(--band-green); }
  .card--grey .card__band { background: var(--band-grey); }
  .brand {
    position: absolute;
    left: 0;
    top: 206px;
    width: 100%;
    text-align: center;
  }
  .brand__name {
    display: inline-flex;
    align-items: center;
    gap: 10px;
    font-weight: 600;
    font-size: 46px;
    letter-spacing: 5px;
    line-height: 1;
    color: var(--logo-green);
  }
  .brand__dot {
    width: 26px;
    height: 26px;
    border-radius: 50%;
    background: var(--logo-accent);
    margin-top: -6px;
  }
  .brand__slogan {
    margin-top: 14px;
    font-weight: 600;
    font-size: 18px;
    letter-spacing: 5.2px;
    color: var(--slogan);
  }
</style>
</head>
<body>
  <section class="card card--green">
    <div class="card__band"></div>
    <div class="brand">
      <div class="brand__name"><span>NEXBYTE INC</span><span class="brand__dot"></span></div>
      <p class="brand__slogan">BUILDING SMARTER SYSTEMS</p>
    </div>
  </section>

  <section class="card card--grey">
    <div class="card__band"></div>
    <div class="brand">
      <div class="brand__name"><span>NEXBYTE INC</span><span class="brand__dot"></span></div>
      <p class="brand__slogan">BUILDING SMARTER SYSTEMS</p>
    </div>
  </section>
</body>
</html>
```